New Innovative Counselling and psychotherapy Service needs Business Card design

Keep it simple and professional. On one side, just company name and logo (perhaps in all blue) and maybe a tag line.

On other side (all white) my name and Qualifications in centre

Industry/Entity Type

Health And Wellness

Contact Information for Business Card

Dara Whelby
Counsellor & Psychotherapist
BSc (Psychol.), BA, Dip. (Couns. & Psych.), PG.Cert (CBT), FGTrK, ONRE

I will also require Mobile no, Email and web site address of which I'll pass on to final designer.

Font styles to use
Sans Serif

Requirements
Must have
• My Logo Only and please use the colours in logo that is in it.
Should not have
• Any other images

```html
<!DOCTYPE html>
<html lang="en">
<head>
<meta charset="utf-8">
<title>Harbour Crest – Business Card</title>
<link href="https://fonts.googleapis.com/css2?family=Arimo:wght@400;700&display=swap" rel="stylesheet">
<style>
  :root {
    --page-bg: #e9e7e3;
    --card-white: #f7f7f7;
    --card-dark: #323232;
    --brand-blue: #4cb6ee;
    --text-grey: #4a4a4a;
    --text-light: #f2f2f2;
    --shadow: rgba(0, 0, 0, 0.18);
  }
  * { box-sizing: border-box; margin: 0; padding: 0; }
  html, body {
    width: 1200px;
    height: 950px;
    overflow: hidden;
    background: var(--page-bg);
    font-family: "Arimo", Arial, sans-serif;
  }
  .canvas {
    position: relative;
    width: 1200px;
    height: 950px;
  }
  .card {
    position: absolute;
    top: 125px;
    width: 400px;
    height: 700px;
    border-radius: 26px;
    box-shadow: 0 10px 24px var(--shadow);
    overflow: hidden;
  }

  /* Front: personal details */
  .card--front {
    left: 170px;
    background: var(--card-white);
    text-align: center;
    color: var(--text-grey);
  }
  .details {
    padding-top: 70px;
  }
  .details__name {
    color: var(--brand-blue);
    font-weight: 700;
    font-size: 30px;
    letter-spacing: 0.3px;
    margin-bottom: 10px;
  }
  .details__role {
    font-size: 19px;
    margin-bottom: 4px;
  }
  .details__quals {
    font-size: 15px;
    line-height: 1.35;
    margin-bottom: 16px;
  }
  .details__contact {
    font-size: 17px;
    line-height: 1.4;
    font-style: normal;
  }
  .front-brand {
    position: absolute;
    left: 0;
    right: 0;
    bottom: 170px;
    display: flex;
    align-items: center;
    justify-content: center;
    gap: 16px;
  }
  .front-brand__dot {
    width: 44px;
    height: 44px;
    border-radius: 50%;
    background: var(--brand-blue);
  }
  .front-brand__name {
    font-size: 38px;
    font-weight: 400;
    color: var(--brand-blue);
  }

  /* Back: company name and tagline */
  .card--back {
    left: 630px;
    background: var(--card-dark);
    color: var(--text-light);
  }
  .back-content {
    position: absolute;
    width: 700px;
    height: 400px;
    left: -150px;
    top: 150px;
    transform: rotate(90deg);
    display: flex;
    flex-direction: column;
    justify-content: center;
    padding-left: 70px;
  }
  .back-brand {
    display: flex;
    align-items: center;
    gap: 22px;
  }
  .back-brand__dot {
    width: 52px;
    height: 52px;
    border-radius: 50%;
    background: var(--brand-blue);
  }
  .back-brand__name {
    font-size: 50px;
    font-weight: 400;
    letter-spacing: 0.5px;
  }
  .tagline {
    margin-top: 14px;
    font-size: 17px;
    letter-spacing: 0.2px;
  }
</style>
</head>
<body>
<main class="canvas">
  <section class="card card--front" aria-label="Business card front">
    <div class="details">
      <h1 class="details__name">Dara Whelby</h1>
      <p class="details__role">Counsellor &amp; Psychotherapist</p>
      <p class="details__quals">MSc (Clin. Psych.), BA, Dip. (Fam. Ther.)<br>PG.Dip (DBT), FGTrK,</p>
      <address class="details__contact">
        (Ph) 555 210 4478<br>
        dara@harbourcrest.com<br>
        www.harbourcrest.com
      </address>
    </div>
    <div class="front-brand">
      <span class="front-brand__dot"></span>
      <span class="front-brand__name">Harbour Crest</span>
    </div>
  </section>

  <section class="card card--back" aria-label="Business card back">
    <div class="back-content">
      <div class="back-brand">
        <span class="back-brand__dot"></span>
        <span class="back-brand__name">Harbour Crest</span>
      </div>
      <p class="tagline">Gentle Support For A Calmer And Stronger Mind</p>
    </div>
  </section>
</main>
</body>
</html>
```